Heron Loan Partners Business Card

We need a business card design for our mortgage servicing company. In addition to servicing the loans of homeowners, we help homeowners with purchasing their homes and any mortgage refinancing. We would like to see designs that use the colors in the logo attached below (gold-ish yellow and navy blue), and any other design you deem fit! The design should communicate a simpler life with smart mortgages provided by Heron.

```html
<!DOCTYPE html>
<html lang="en">
<head>
<meta charset="utf-8">
<title>Heron Loan Partners Business Card</title>
<link rel="stylesheet" href="https://fonts.googleapis.com/css2?family=Montserrat:wght@800&family=Poppins:wght@400;600;700&display=swap">
<style>
  :root {
    --navy: #221f52;
    --gold: #ddb13f;
    --white: #ffffff;
    --ink: #1d1b3a;
    --page: #ffffff;
  }
  * { margin: 0; padding: 0; box-sizing: border-box; }
  html, body { width: 1200px; height: 2298px; overflow: hidden; background: var(--page); }
  body { position: relative; font-family: "Poppins", sans-serif; }

  .card {
    position: absolute;
    left: 180px;
    width: 840px;
    height: 479px;
    overflow: hidden;
    background: var(--white);
    box-shadow: 0 4px 14px rgba(0,0,0,0.28);
  }
  .card--front { top: 590px; }
  .card--back { top: 1229px; }

  .card__art { position: absolute; inset: 0; width: 100%; height: 100%; }

  .brand-name {
    position: absolute;
    color: var(--gold);
    font-family: "Poppins", sans-serif;
    font-weight: 700;
    white-space: nowrap;
    text-align: center;
    transform: translateX(-50%);
  }
  .card--front .brand-name { left: 420px; top: 210px; font-size: 38px; }
  .card--back .brand-name { left: 226px; top: 218px; font-size: 31px; }

  .website-line {
    position: absolute;
    left: 0; right: 0;
    top: 343px;
    text-align: center;
    color: var(--navy);
    font-weight: 600;
    font-size: 29px;
    letter-spacing: 4px;
    padding-left: 10px;
  }

  .band { position: absolute; left: 0; width: 100%; background: var(--navy); }
  .band--top { top: 0; height: 75px; }
  .band--bottom { bottom: 0; height: 77px; }

  .divider {
    position: absolute;
    left: 461px; top: 104px;
    width: 3px; height: 256px;
    background: var(--ink);
  }

  .contact { position: absolute; left: 514px; top: 108px; color: var(--navy); }
  .contact__name {
    font-family: "Montserrat", sans-serif;
    font-weight: 800;
    font-size: 29px;
    line-height: 1.1;
    letter-spacing: 0.2px;
  }
  .contact__role { font-size: 21px; line-height: 1.3; color: var(--ink); }
  .contact__list { list-style: none; margin-top: 14px; }
  .contact__item {
    display: flex; align-items: flex-start;
    font-size: 21px; line-height: 25px; color: var(--ink);
    margin-bottom: 11px;
  }
  .contact__icon {
    flex: none;
    width: 26px; height: 24px;
    margin-right: 20px;
    border-radius: 5px;
    background: var(--gold);
    display: flex; align-items: center; justify-content: center;
  }
  .contact__icon svg { width: 13px; height: 13px; }
</style>
</head>
<body>

<section class="card card--front" aria-label="Card front">
  <svg class="card__art" viewBox="0 0 840 479" aria-hidden="true">
    <rect width="840" height="479" fill="var(--navy)"/>
    <polygon points="231,0 756,0 603,479 84,479" fill="var(--gold)"/>
    <polygon points="240,0 748,0 595,479 93,479" fill="var(--white)"/>
  </svg>
  <div role="img" aria-label="Faint line drawing of a leaping fish on the left navy panel" style="position:absolute;left:0;top:0;width:150px;height:479px;background:var(--navy);opacity:0"></div>
  <div role="img" aria-label="Faint line drawing of a leaping fish on the right navy panel" style="position:absolute;right:0;top:0;width:130px;height:479px;background:var(--navy);opacity:0"></div>
  <div class="brand-name">Heron Loan Partners</div>
  <div class="website-line">www.heronloans.com</div>
</section>

<section class="card card--back" aria-label="Card back">
  <div class="band band--top" role="img" aria-label="Navy band with faint fish line drawing"></div>
  <div class="band band--bottom" role="img" aria-label="Navy band with faint fish line drawing"></div>
  <div class="brand-name">Heron Loan Partners</div>
  <div class="divider"></div>
  <div class="contact">
    <h1 class="contact__name">SAMUEL J. HARPER</h1>
    <p class="contact__role">CEO/Founder</p>
    <ul class="contact__list">
      <li class="contact__item">
        <span class="contact__icon"><svg viewBox="0 0 16 16"><path d="M4 1.5 6.2 4 5 5.6c.9 2 2.5 3.6 4.4 4.4L11 8.8l2.5 2.2-1.3 2.4C7 13.4 2.6 9 2.6 3.8Z" fill="var(--navy)"/></svg></span>
        (888)-555-0142
      </li>
      <li class="contact__item">
        <span class="contact__icon"><svg viewBox="0 0 16 16"><path d="M8 1a4.5 4.5 0 0 0-4.5 4.5C3.5 9 8 15 8 15s4.5-6 4.5-9.5A4.5 4.5 0 0 0 8 1Zm0 6.3a1.8 1.8 0 1 1 0-3.6 1.8 1.8 0 0 1 0 3.6Z" fill="var(--navy)"/></svg></span>
        <span>218 Harbor Ave S,<br>Bayview, FL 33000</span>
      </li>
      <li class="contact__item">
        <span class="contact__icon"><svg viewBox="0 0 16 16"><rect x="1.5" y="3.5" width="13" height="9" rx="1" fill="var(--navy)"/><path d="M2 4.2 8 8.6l6-4.4" stroke="var(--gold)" stroke-width="1.2" fill="none"/></svg></span>
        info@heronloans.com
      </li>
      <li class="contact__item">
        <span class="contact__icon"><svg viewBox="0 0 16 16"><circle cx="8" cy="8" r="6.3" fill="none" stroke="var(--navy)" stroke-width="1.4"/><ellipse cx="8" cy="8" rx="2.6" ry="6.3" fill="none" stroke="var(--navy)" stroke-width="1.2"/><path d="M1.8 8h12.4M2.8 5h10.4M2.8 11h10.4" stroke="var(--navy)" stroke-width="1.1"/></svg></span>
        www.heronloans.com
      </li>
    </ul>
  </div>
</section>

</body>
</html>
```